Dunmore Roofing

Want a professional looking business card

Industry/Entity Type

Business

Contact Information for Business Card

Paul Dunmore ( Owner) paul@dunmoreroofing-example.com, www.dunmoreroofing-example.com, Adress: 4172 Township road 43 Larkfield,ON K9X4T2

```html
<!DOCTYPE html>
<html lang="en">
<head>
<meta charset="utf-8">
<title>Dunmore Roofing — Business Card</title>
<link rel="stylesheet" href="https://fonts.googleapis.com/css2?family=Roboto+Condensed:wght@700&family=Open+Sans:wght@400&display=swap">
<style>
  :root {
    --page-bg: #ececec;
    --card-white: #ffffff;
    --brand-blue: #1b4688;
    --soft-grey: #e4e4e5;
    --role-light: #dfe4ee;
    --back-grey: #6d6e70;
    --rule-grey: #b9bbbe;
    --text-white: #ffffff;
  }
  * { box-sizing: border-box; margin: 0; padding: 0; }
  html, body { width: 940px; height: 1200px; overflow: hidden; }
  body {
    background: var(--page-bg);
    position: relative;
    font-family: "Open Sans", Arial, sans-serif;
  }
  .card {
    position: absolute;
    left: 239px;
    width: 515px;
    height: 295px;
    overflow: hidden;
    box-shadow: 0 3px 8px rgba(0,0,0,0.18);
  }
  .card-front { top: 62px; background: var(--card-white); }
  .card-back  { top: 520px; background: var(--back-grey); }

  .front-decor { position: absolute; left: 0; top: 0; }

  .brand-name {
    position: absolute;
    left: 24px;
    top: 70px;
    font-family: "Roboto Condensed", Arial, sans-serif;
    font-weight: 700;
    font-size: 30px;
    line-height: 34px;
    letter-spacing: 1px;
    color: var(--brand-blue);
    text-transform: uppercase;
  }

  .holder {
    position: absolute;
    right: 18px;
    top: 152px;
    text-align: right;
    z-index: 2;
  }
  .holder-name {
    font-family: "Roboto Condensed", Arial, sans-serif;
    font-weight: 700;
    font-size: 19px;
    color: var(--brand-blue);
    text-transform: uppercase;
    line-height: 24px;
  }
  .holder-role {
    margin-top: 0;
    font-size: 11px;
    color: var(--role-light);
    text-transform: uppercase;
    line-height: 20px;
  }

  .contact-band {
    position: absolute;
    left: 0; top: 175px;
    width: 100%; height: 120px;
    background: var(--brand-blue);
    border-top: 2px solid var(--rule-grey);
    color: var(--text-white);
    font-size: 13.5px;
    line-height: 19.5px;
    z-index: 1;
  }
  .address { position: absolute; left: 23px; top: 43px; font-style: normal; }
  .contact-list {
    position: absolute; right: 18px; top: 43px;
    list-style: none; text-align: right;
  }
  .contact-list li { display: flex; align-items: center; justify-content: flex-end; gap: 6px; }
  .contact-list svg { width: 15px; height: 15px; flex: none; }

  .back-brand {
    position: absolute;
    left: 0; right: 0; top: 118px;
    text-align: center;
    font-family: "Roboto Condensed", Arial, sans-serif;
    font-weight: 700;
    font-size: 34px;
    letter-spacing: 2px;
    color: var(--text-white);
    text-transform: uppercase;
  }
  .back-web {
    position: absolute;
    left: 24px; bottom: 22px;
    font-size: 12px;
    color: var(--text-white);
  }
</style>
</head>
<body>

<section class="card card-front" aria-label="Business card front">
  <svg class="front-decor" width="515" height="175" viewBox="0 0 515 175" aria-hidden="true">
    <polygon points="429,0 456,0 302,175 275,175" fill="var(--soft-grey)"/>
    <rect x="431" y="73" width="30" height="30" fill="var(--soft-grey)"/>
    <rect x="466" y="73" width="30" height="30" fill="var(--soft-grey)"/>
    <rect x="431" y="108" width="30" height="30" fill="var(--soft-grey)"/>
    <rect x="466" y="108" width="30" height="30" fill="var(--soft-grey)"/>
  </svg>

  <div class="brand-name">Dunmore<br>Roofing</div>

  <div class="holder">
    <div class="holder-name">Paul Dunmore</div>
    <div class="holder-role">Owner</div>
  </div>

  <div class="contact-band">
    <address class="address">
      Dunmore Roofing<br>
      4172 Township road 43,<br>
      Larkfield,ON K9X4T2
    </address>
    <ul class="contact-list">
      <li>(613) 555-0147
        <svg viewBox="0 0 16 16" aria-hidden="true"><circle cx="8" cy="8" r="8" fill="#fff"/><path d="M5.2 4.2l1.4-.3.9 2-1 .8a6 6 0 0 0 2.8 2.8l.8-1 2 .9-.3 1.4c-.2.6-.8.9-1.5.8A7.5 7.5 0 0 1 4.4 5.7c-.1-.7.2-1.3.8-1.5z" fill="var(--brand-blue)"/></svg>
      </li>
      <li>paul@dunmoreroofing-example.com
        <svg viewBox="0 0 16 16" aria-hidden="true"><circle cx="8" cy="8" r="8" fill="#fff"/><rect x="4" y="5" width="8" height="6" fill="var(--brand-blue)"/><path d="M4 5l4 3.2L12 5" stroke="#fff" stroke-width="0.9" fill="none"/></svg>
      </li>
      <li>www.dunmoreroofing-example.com
        <svg viewBox="0 0 16 16" aria-hidden="true"><circle cx="8" cy="8" r="8" fill="#fff"/><circle cx="8" cy="8" r="4.3" fill="none" stroke="var(--brand-blue)" stroke-width="1"/><ellipse cx="8" cy="8" rx="1.8" ry="4.3" fill="none" stroke="var(--brand-blue)" stroke-width="0.9"/><path d="M3.7 8h8.6" stroke="var(--brand-blue)" stroke-width="0.9"/></svg>
      </li>
    </ul>
  </div>
</section>

<section class="card card-back" aria-label="Business card back">
  <div class="back-brand">Dunmore Roofing</div>
  <div class="back-web">www.dunmoreroofing-example.com</div>
</section>

</body>
</html>
```